Kestrelbrook Student Accomodation needs a business card design

Hi Guys,

We are a Student Accommodation company in Australia. We already have a logo which I will submit.

I will require the design of the business cards from you.

I am after something that looks clean, modern and that people feel interested and actually want to contact us.

We would like to see designs that are innovative.

On the business cards I will require to have:

Employee Name
Position
Phone number
Email
Facebook page

I hope you can help me with this project guys as I have heard really good things from you.

```html
<!DOCTYPE html>
<html lang="en">
<head>
<meta charset="utf-8">
<title>Kestrelbrook Student Accomodation – Business Card</title>
<link rel="stylesheet" href="https://fonts.googleapis.com/css2?family=Lato:wght@400;700;900&display=swap">
<style>
  :root {
    --green: #0a8a3a;
    --gold: #f2b01e;
    --white: #ffffff;
    --ink: #2b2b2b;
    --backdrop: #e9e9e7;
    --card-shadow: rgba(0, 0, 0, 0.16);
  }
  * { box-sizing: border-box; margin: 0; padding: 0; }
  html, body { width: 1200px; height: 680px; overflow: hidden; }
  body {
    background: var(--backdrop);
    font-family: "Lato", Arial, sans-serif;
    position: relative;
  }
  .card {
    position: absolute;
    top: 185px;
    width: 540px;
    height: 310px;
    border-radius: 22px;
    background: var(--white);
    overflow: hidden;
    box-shadow: 0 10px 28px var(--card-shadow);
  }
  .card--front { left: 40px; }
  .card--back { left: 620px; }

  .card__artwork { position: absolute; inset: 0; overflow: hidden; }

  .brand {
    position: absolute;
    display: flex;
    align-items: center;
    gap: 12px;
  }
  .brand__square {
    width: 30px;
    height: 30px;
    background: var(--gold);
    flex: none;
  }
  .brand__name {
    color: var(--green);
    font-weight: 900;
    font-size: 19px;
    line-height: 1.15;
    text-transform: uppercase;
    letter-spacing: 0.5px;
  }
  .card--front .brand { left: 40px; top: 66px; width: 200px; }

  .contact {
    position: absolute;
    left: 300px;
    top: 160px;
    list-style: none;
    color: var(--white);
    font-size: 14.5px;
    line-height: 21px;
  }
  .contact__item { display: flex; align-items: center; gap: 10px; }
  .contact__icon { width: 14px; height: 14px; flex: none; }

  .person {
    position: absolute;
    left: 40px;
    top: 248px;
    color: var(--white);
  }
  .person__name { font-size: 19px; font-weight: 400; }
  .person__role { font-size: 14px; margin-top: 1px; }

  .card--back .brand {
    left: 50%;
    top: 110px;
    transform: translateX(-50%);
    width: 340px;
  }
  .card--back .brand__square { width: 44px; height: 44px; }
  .card--back .brand__name { font-size: 26px; }
  .social-line {
    position: absolute;
    right: 36px;
    bottom: 28px;
    font-size: 14px;
    letter-spacing: 2px;
    color: var(--ink);
  }
</style>
</head>
<body>

<section class="card card--front" aria-label="Business card front">
  <svg class="card__artwork" width="540" height="310" viewBox="0 0 540 310" aria-hidden="true">
    <path d="M198 186 C 280 140, 345 80, 372 -10 L 550 -10 L 550 320 L 198 320 Z" fill="var(--gold)"/>
    <path d="M-10 231 C 200 222, 340 140, 404 -10 L 550 -10 L 550 320 L -10 320 Z" fill="var(--green)" stroke="var(--white)" stroke-width="7"/>
  </svg>

  <div class="brand">
    <span class="brand__square"></span>
    <span class="brand__name">Kestrelbrook Student Accomodation</span>
  </div>

  <ul class="contact">
    <li class="contact__item">
      <svg class="contact__icon" viewBox="0 0 16 16" aria-hidden="true"><path d="M3.5 1.5l2.5 3-1.5 1.8a9 9 0 0 0 5.2 5.2l1.8-1.5 3 2.5-1.6 2.3C7 14.5 1.5 9 1.2 3.1z" fill="var(--gold)"/></svg>
      <span>040 555 0172</span>
    </li>
    <li class="contact__item">
      <svg class="contact__icon" viewBox="0 0 16 16" aria-hidden="true"><rect x="1" y="3.5" width="14" height="9" rx="1" fill="var(--gold)"/><path d="M1.5 4l6.5 5 6.5-5" fill="none" stroke="var(--green)" stroke-width="1.3"/></svg>
      <span>info@kestrelbrook.example</span>
    </li>
    <li class="contact__item">
      <svg class="contact__icon" viewBox="0 0 16 16" aria-hidden="true"><circle cx="8" cy="4.5" r="3" fill="var(--gold)"/><path d="M2.5 15a5.5 5.5 0 0 1 11 0z" fill="var(--gold)"/></svg>
      <span>fb.example/kestrelbrook</span>
    </li>
  </ul>

  <div class="person">
    <p class="person__name">Marcus Ellery</p>
    <p class="person__role">manager</p>
  </div>
</section>

<section class="card card--back" aria-label="Business card back">
  <div class="brand">
    <span class="brand__square"></span>
    <span class="brand__name">Kestrelbrook Student Accomodation</span>
  </div>
  <p class="social-line">fb.example/kestrelbrook</p>
</section>

</body>
</html>
```